I need a label with logo to go on jars of honey.
Label size 70mm x 70mm
The front label should say :
The Fenwick Honey Co. (logo)
Tarapeka Honey
400g
The back label:
Would have nutritional information
And our address
You can see from the uploaded files the styles I prefer, I have uploaded a photo of the honey product too. The background of the logo doesn't have to be white. I would like to develop a color scheme that would look nice against the color of the honey.
Logo Text
The Fenwick Honey Co. / The Fenwick Honey Company

```html
<!DOCTYPE html>
<html lang="en">
<head>
<meta charset="utf-8">
<title>The Fenwick Honey Co. — Tarapeka Honey Jar Labels</title>
<link href="https://fonts.googleapis.com/css2?family=Anton&family=Montserrat:wght@500;600;700;800&family=Arimo:wght@400;700&display=swap" rel="stylesheet">
<style>
  :root {
    --cocoa: #2b1714;
    --cocoa-deep: #231210;
    --honey: #f39a12;
    --honey-deep: #e0780a;
    --honey-light: #fbb83a;
    --paper: #ffffff;
    --paper-shade: #f1f1f1;
    --ink: #1c1412;
    --stage: #d1d1d1;
  }
  * { box-sizing: border-box; margin: 0; padding: 0; }
  html, body { width: 946px; height: 1200px; overflow: hidden; }
  body {
    background: var(--stage);
    font-family: "Montserrat", Arial, sans-serif;
    color: var(--ink);
    position: relative;
  }
  .label {
    position: absolute;
    left: 193px;
    width: 560px;
    height: 560px;
    overflow: hidden;
    background: linear-gradient(180deg, var(--paper) 0%, var(--paper-shade) 100%);
  }
  .label--front { top: 26px; }
  .label--back { top: 614px; }

  /* front */
  .brand-band {
    position: absolute; left: 0; top: 0; width: 100%; height: 216px;
    background: radial-gradient(ellipse at 50% 40%, #3a211c 0%, var(--cocoa) 55%, var(--cocoa-deep) 100%);
  }
  .brand {
    position: absolute; left: 0; width: 100%;
    display: flex; align-items: center; justify-content: center; gap: 12px;
    font-weight: 700; text-transform: uppercase; white-space: nowrap;
  }
  .brand__dot { border-radius: 50%; background: var(--honey); flex: none; }
  .brand-band .brand { top: 86px; font-size: 29px; color: var(--honey); }
  .brand-band .brand__dot { width: 38px; height: 38px; }

  .product-name {
    position: absolute; left: 0; width: 100%; text-align: center;
    font-family: "Anton", "Impact", sans-serif; text-transform: uppercase; line-height: 1;
  }
  .product-name--place { top: 228px; font-size: 128px; color: var(--cocoa); letter-spacing: -1px; }
  .product-name--kind { top: 392px; font-size: 98px; color: var(--honey); }

  .divider {
    position: absolute; top: 372px; left: 125px; width: 310px; height: 12px;
    display: flex; align-items: center; justify-content: space-between;
  }
  .divider__rule { width: 108px; height: 1.5px; background: var(--cocoa); }
  .divider__mark { width: 12px; height: 12px; border-radius: 50%; background: var(--cocoa); }

  .comb-band {
    position: absolute; left: 0; bottom: 0; width: 100%; height: 63px;
    background: linear-gradient(180deg, var(--honey-light) 0%, var(--honey) 45%, var(--honey-deep) 100%);
  }
  .net-weight {
    position: absolute; left: 174px; top: 519px; width: 214px; height: 30px;
    background: var(--paper); border-radius: 15px;
    font-size: 15px; font-weight: 500; color: var(--ink);
    display: flex; align-items: center; justify-content: center;
  }

  /* back */
  .label--back .brand { top: 104px; left: 31px; width: 320px; font-size: 15px; color: var(--cocoa); gap: 8px; }
  .label--back .brand__dot { width: 16px; height: 16px; }
  .info { position: absolute; left: 31px; top: 143px; width: 320px; font-size: 9.6px; line-height: 13.4px; }
  .info h3 { font-size: 10px; font-weight: 700; }
  .info p { font-weight: 500; text-align: justify; margin-bottom: 8px; }

  .nutrition {
    position: absolute; left: 355px; top: 32px; width: 168px;
    border: 1px solid #888; background: var(--paper);
    padding: 3px 5px 4px; font-family: "Arimo", Arial, sans-serif; font-size: 8.3px; line-height: 1.2;
  }
  .nutrition h2 { font-size: 19px; font-weight: 700; line-height: 1; }
  .nutrition .row { display: flex; justify-content: space-between; border-top: 0.8px solid #444; padding: 1.8px 0; }
  .nutrition .row--sub { padding-left: 8px; }
  .nutrition .thick { border-top: 5px solid var(--ink); }
  .nutrition .mid { border-top: 2.5px solid var(--ink); }
  .nutrition .tiny { font-size: 6px; font-weight: 700; justify-content: flex-end; }
  .nutrition .note { font-size: 5.6px; border-top: 0.8px solid #444; padding-top: 2px; }
  .nutrition b { font-weight: 700; }

  .message-band {
    position: absolute; left: 0; top: 344px; width: 100%; height: 107px;
    background: var(--cocoa);
    color: var(--paper); font-weight: 800; font-size: 11.6px; line-height: 17px;
    text-transform: uppercase; text-align: center;
    display: flex; align-items: center; justify-content: center; padding: 0 18px;
  }
  .web {
    position: absolute; left: 0; top: 466px; width: 100%; text-align: center;
    font-weight: 800; font-size: 17px; color: var(--ink);
  }
</style>
</head>
<body>

<section class="label label--front" aria-label="Front label">
  <div class="brand-band" role="img" aria-label="Dark chocolate brown band with a faint honeycomb texture">
    <div class="brand"><span class="brand__dot"></span>The Fenwick Honey Co.</div>
  </div>
  <h1 class="product-name product-name--place">Tarapeka</h1>
  <div class="divider"><span class="divider__rule"></span><span class="divider__mark"></span><span class="divider__rule"></span></div>
  <div class="product-name product-name--kind">Honey</div>
  <div class="comb-band" role="img" aria-label="Golden honeycomb pattern band"></div>
  <div class="net-weight">Net Wt.16 oz. (400g)</div>
</section>

<section class="label label--back" aria-label="Back label">
  <div class="brand"><span class="brand__dot"></span>The Fenwick Honey Co.</div>

  <div class="info">
    <h3>INGREDIENTS:</h3>
    <p>Lorem Ipsum is simply dummy text of the printing and typesetting industry. Lorem Ipsum has been the industry's standard dummy text ever since the 1500s, when an unknown printer took a galley of type and scrambled it to make a type specimen book. It has survived not only five centuries, but also the leap into electronic typesetting, remaining essentially unchanged.</p>
    <h3>CAUTION:</h3>
    <p>Lorem Ipsum is simply dummy text of the printing and typesetting industry. Lorem Ipsum has been the industry's standard dummy text ever since the 1500s, when an unknown printer took a galley of type and scrambled it.</p>
  </div>

  <div class="nutrition">
    <h2>Nutrition Facts</h2>
    <div>Serving Size 1 packet (45g)</div>
    <div class="row thick"><b style="font-size:6.5px">Amount Per Serving</b></div>
    <div class="row"><span><b>Calories</b> 120</span><span>Calories from Fat 0</span></div>
    <div class="row mid tiny">% Daily Value*</div>
    <div class="row"><span><b>Total Fat</b> 0g</span><b>0%</b></div>
    <div class="row row--sub"><span>Saturated Fat 0g</span><b>0%</b></div>
    <div class="row row--sub"><span>Trans Fat 0g</span><span></span></div>
    <div class="row"><span><b>Cholesterol</b> 0mg</span><b>0%</b></div>
    <div class="row"><span><b>Sodium</b> 90mg</span><b>4%</b></div>
    <div class="row"><span><b>Potassium</b> 40mg</span><b>1%</b></div>
    <div class="row"><span><b>Total Carbohydrate</b> 34g</span><b>11%</b></div>
    <div class="row row--sub"><span>Dietary Fiber 0g</span><b>0%</b></div>
    <div class="row row--sub"><span>Sugars 34g</span><span></span></div>
    <div class="row"><span><b>Protein</b> 0g</span><span></span></div>
    <div class="row thick"><span>Vitamin A 0%</span><span>•&nbsp; Vitamin C 0%</span></div>
    <div class="row"><span>Calcium 2%</span><span>•&nbsp; Iron 0%</span></div>
    <div class="row"><span>Magnesium 2%</span><span></span></div>
    <div class="note">*Percent Daily Values are based on a 2,000 calorie diet.</div>
  </div>

  <div class="message-band">Lorem Ipsum is simply dummy text of the printing and typesetting industry. Lorem Ipsum has been the industry's standard dummy text ever since the 1500s, when an unknown printer took</div>
  <div class="web">WWW.FENWICKHONEYCO.NZ</div>
  <div class="comb-band" role="img" aria-label="Golden honeycomb pattern band"></div>
</section>

</body>
</html>
```